Commercial/Corporate Law Firm needs Website Design

Hi guys. I've started up a new law firm and would love your help designing an attractive website. I'll need both design and coding, and to make it easy for us to edit as necessary later, I think it should be built off a Wordpress.org structure.
FIRST IMPRESSIONS
It's very important that the first impression of the website really captures our prospective clients' attention and impresses them. Their first three seconds needs to be good.
I imagine the homepage may be short, with a menu bar and a compelling image, and with a tagline overlaid or underneath (eg. "It's about results.")
The image should be related to our practice areas: eg. IPOs, corporate transactions, or commercial negotiations.
I have previously suggested there could be a skyline image of Sydney or Adelaide. However, because we are based in Adelaide, I don't think Sydney is appropriate - and Adelaide is probably too boring to use.
HOMEPAGE
Being a new firm, we don't have many existing testimonials, and I will be the only lawyer to start with. So we need to focus on the nature of the services we will provide and how my experience can help them. We have an existing logo to use, and I would like the website colour scheme not to clash with that logo (dark blue and white).
After the initial image and tagline there should be a brief introduction to each of the main areas of work, eg. "We specialise in three main areas of practice:"
1. Corporate Transactions and Regulation
2. Business Law and Dispute Resolution
3. Migration Assistance
These should each have an appropriate photo and link to a separate page that briefly describes our services in that area.
Below that there should be a message from me with a photo. Finally, at the bottom, there should be a "Contact Us" section which shows a Google image of our address, contact details, and then our logo with colours inverted.
OTHER PAGES
While we will need some other pages, they should all be fairly simple. I think we will need one page to say "About Us", where I will put information about my experience. I think we will then need one page for each of the 3 areas listed above, which just needs an appropriate image and then text to describe the service. Finally, a "Contact Us" page which I imagine will be the same as the bottom of the homepage.
OTHER DETAILS
For now you can use details from my LinkedIn page to fill out any other text as necessary, or the photo.
Because the logo is square, I would prefer the design of the website also to be rectangular.
Looking forward to seeing your work! Thank you.
Marcus
Potential clients:
Businesses with legal issues or disputes
Companies wishing to list on the stock market

```html
<!DOCTYPE html>
<html lang="en">
<head>
<meta charset="utf-8">
<title>Halden Legal</title>
<link rel="stylesheet" href="https://fonts.googleapis.com/css2?family=Arimo:wght@400;700&family=Mulish:wght@400;600&display=swap">
<style>
:root{
  --navy:#1e3a6b;
  --navy-deep:#172d52;
  --navy-bar:#1a3056;
  --grey-btn:#808080;
  --text:#555;
  --text-light:#777;
  --white:#fff;
  --line:#ddd;
}
*{margin:0;padding:0;box-sizing:border-box}
html,body{width:1200px;height:3031px;overflow:hidden}
body{position:relative;background:var(--white);font-family:"Arimo",Arial,sans-serif;color:var(--text)}
.abs{position:absolute}
a{color:inherit}

/* header */
.brand{left:77px;top:14px;width:170px;height:108px;display:flex;flex-direction:column;align-items:center;justify-content:center;gap:4px;color:var(--navy);font-family:"Mulish",sans-serif;font-weight:600}
.brand .mark{width:56px;height:56px;background:var(--navy)}
.brand .name{font-size:25px;letter-spacing:2px;line-height:1}
.brand .sub{font-size:13px;letter-spacing:9px;line-height:1}
.top-info{display:flex;align-items:flex-start;gap:22px;font-size:14.5px;line-height:25px;color:var(--text-light)}
.icon-box{width:44px;height:44px;border:2px solid var(--navy);display:flex;align-items:center;justify-content:center;flex:none}

/* nav */
.nav{left:0;top:135px;width:1200px;height:52px;background:var(--navy)}
.nav ul{list-style:none;display:flex;position:absolute;left:78px;top:0;height:52px}
.nav li{height:52px;line-height:52px;color:var(--white);font-size:16.5px;padding:0 15px;margin-right:14px}
.nav li.active{background:var(--grey-btn)}
.quote{right:78px;top:0;width:249px;height:52px;line-height:52px;background:var(--grey-btn);color:var(--white);font-weight:700;font-size:17px;text-align:center;letter-spacing:.5px}

/* hero */
.hero{left:0;top:187px;width:1200px;height:552px;background:linear-gradient(180deg,#3b4350 0%,#8a6a45 45%,#c98a45 60%,#3a2c24 100%)}
.hero-portrait{right:0;top:0;width:420px;height:552px;background:linear-gradient(180deg,rgba(40,40,55,.1),rgba(30,30,45,.7))}
.hero h1{left:79px;top:380px;font-size:47px;font-weight:700;color:var(--white);letter-spacing:.5px}
.hero-text{left:79px;top:457px;width:500px;font-size:16.5px;line-height:27px;color:var(--white)}

/* sections */
.section-title{left:0;width:1200px;text-align:center;color:var(--navy);font-weight:700;letter-spacing:.5px}
.intro{left:180px;width:840px;text-align:center;font-size:14.5px;line-height:25px}
.card{top:963px;width:322px;text-align:center}
.card .photo{height:218px}
.card h3{font-family:"Mulish",sans-serif;font-weight:400;color:var(--navy);font-size:24px;line-height:35px;margin-top:20px}
.card p{font-family:"Mulish",sans-serif;font-size:14.5px;line-height:25px;color:var(--text-light);margin-top:8px;padding:0 18px}
.card .more{display:block;margin-top:10px;color:var(--navy);font-weight:700;font-size:17px;text-decoration:underline}

.welcome{left:0;top:1458px;width:1200px;height:384px;background:linear-gradient(100deg,#2a4577,#1f3a6a 50%,#2c4a7e)}
.welcome h2{top:52px;font-size:44px;color:var(--white)}
.welcome p{left:150px;width:900px;text-align:center;font-size:14.5px;line-height:25px;color:var(--white)}
.btn{left:506px;top:270px;width:187px;height:47px;background:var(--white);color:var(--navy-deep);font-weight:700;font-size:20px;line-height:47px;text-align:center}

.news-photo{width:500px;height:292px}
.date{width:68px;height:73px;background:#f0f0f0;border:1px solid var(--line);font-size:34px;font-weight:700;color:#333;text-align:center;line-height:80px;overflow:hidden}
.date::before{content:"";position:absolute;left:0;top:0;border-top:22px solid var(--navy);border-right:22px solid transparent}
.news-title{font-family:"Mulish",sans-serif;font-size:22px;color:var(--text);letter-spacing:.3px}
.meta{font-size:15px;color:var(--text-light);display:flex;gap:26px;align-items:center}
.meta span{display:flex;align-items:center;gap:9px}
.news-text{width:480px;font-size:14.5px;line-height:25px;color:var(--text-light)}

/* footer */
.footer{left:0;top:2666px;width:1200px;height:313px;background:var(--navy)}
.footer .brand{left:0;top:80px;width:407px;height:160px;color:var(--white);gap:8px}
.footer .brand .mark{width:80px;height:80px;background:transparent;border:3px solid var(--white)}
.footer .brand .name{font-size:38px;letter-spacing:3px}
.footer .brand .sub{font-size:20px;letter-spacing:15px}
.footer h4{font-family:"Mulish",sans-serif;font-weight:400;color:var(--white);font-size:24px}
.contact-list{left:437px;top:93px;list-style:none;color:var(--white);font-size:14.5px;line-height:25px}
.contact-list li{display:flex;gap:14px;margin-bottom:13px}
.contact-list svg{flex:none;margin-top:4px}
.map{left:800px;top:93px;width:261px;height:156px;background:linear-gradient(135deg,#e9efe6,#cfe2c2 60%,#b7d4ee);border:2px solid var(--white)}
.copyright{left:0;top:2979px;width:1200px;height:52px;background:var(--navy-bar);color:var(--white);font-size:15.5px;text-align:center;line-height:52px}
</style>
</head>
<body>

<div class="abs brand"><div class="mark"></div><div class="name">HALDEN</div><div class="sub">LEGAL</div></div>

<div class="abs top-info" style="left:609px;top:42px;width:330px">
  <div class="icon-box"><svg width="18" height="22" viewBox="0 0 18 22"><path d="M9 1a7 7 0 0 1 7 7c0 5-7 13-7 13S2 13 2 8a7 7 0 0 1 7-7z" fill="none" stroke="#1e3a6b" stroke-width="2"/><circle cx="9" cy="8" r="2.5" fill="#1e3a6b"/></svg></div>
  <div style="margin-top:-3px">Lorem Ipsum is simply dummy text<br>of the printing and typesetting.</div>
</div>
<div class="abs top-info" style="left:963px;top:42px;width:170px">
  <div class="icon-box"><svg width="22" height="22" viewBox="0 0 24 24"><path d="M6 2l4 4-2 3c1 3 4 6 7 7l3-2 4 4-3 4C10 21 3 14 2 5z" fill="#1e3a6b"/></svg></div>
  <div style="margin-top:-3px">Call Us<br>123 456<br>7890</div>
</div>

<nav class="abs nav">
  <ul><li class="active">HOME</li><li>ABOUT</li><li style="margin-right:16px">PRACTICE AREAS</li><li>TESTIMONIALS</li><li>CONTACT</li></ul>
  <div class="abs quote">REAQUEST A FREE QUOTE</div>
</nav>

<section class="abs hero" role="img" aria-label="City skyline at sunset with a smiling lawyer in a suit">
  <div class="abs hero-portrait"></div>
</section>
<h1 class="abs hero" style="background:none;width:auto;height:auto;left:79px;top:380px;font-size:47px;color:#fff">IT'S ABOUT RESULT</h1>
<p class="abs hero-text">Lorem Ipsum is simply dummy text of the printing and typesetting industry. Lorem Ipsum has been the industry's standard dummy text ever since the 1500s, when an unknown printer took a galley.</p>

<h2 class="abs section-title" style="top:808px;font-size:42px">PRACTICE AREAS</h2>
<p class="abs intro" style="top:868px">Lorem Ipsum is simply dummy text of the printing and typesetting industry. Lorem Ipsum has been the industry's standard dummy text ever since the 1500s, when an unknown printer took a galley of type.</p>

<div class="abs card" style="left:78px">
  <div class="photo" role="img" aria-label="Lawyer meeting a client at an office desk" style="background:linear-gradient(135deg,#e8e6e2,#b9a58c 60%,#6c5a49)"></div>
  <h3>Business Law and<br>Dispute Resolution</h3>
  <p>Lorem Ipsum is simply dummy text of the printing and typesetting industry. Lorem Ipsum has been the industry's standard.</p>
  <a class="more">READ MORE</a>
</div>
<div class="abs card" style="left:439px">
  <div class="photo" role="img" aria-label="Hand holding a passport" style="background:linear-gradient(135deg,#d8d4cf,#2b3f8a 55%,#15214d)"></div>
  <h3>Migration Assistance</h3>
  <p>Lorem Ipsum is simply dummy text of the printing and typesetting industry. Lorem Ipsum has been the industry's standard dummy text ever since the 1500s.</p>
  <a class="more" style="margin-top:12px">READ MORE</a>
</div>
<div class="abs card" style="left:800px">
  <div class="photo" role="img" aria-label="Agreement papers with glasses, pen and calculator" style="background:linear-gradient(135deg,#d9dde0,#f1efea 50%,#3c3f44)"></div>
  <h3>Corporate Transactions<br>and Regulation</h3>
  <p>Lorem Ipsum is simply dummy text of the printing and typesetting industry. Lorem Ipsum has been the industry's standard.</p>
  <a class="more">READ MORE</a>
</div>

<section class="abs welcome" role="img" aria-label="Business people signing documents, tinted blue">
  <h2 class="abs section-title" style="top:50px;font-size:44px;color:#fff">WELCOME TO HALDEN LEGAL</h2>
  <p class="abs" style="top:110px">Lorem Ipsum is simply dummy text of the printing and typesetting industry. Lorem Ipsum has been the industry's standard dummy text ever since the 1500s, when an unknown printer took a galley of type and scrambled it to make a type specimen book. It has survived not only five centuries, but also the leap into electronic typesetting, remaining essentially unchanged.</p>
  <p class="abs" style="top:200px">Lorem Ipsum is simply dummy text of the printing and typesetting industry. Lorem Ipsum has been the industry's standard dummy text ever since the 1500s, when an unknown printer took a galley of type and scrambled it to make a type.</p>
  <div class="abs btn">READ MORE</div>
</section>

<h2 class="abs section-title" style="top:1890px;font-size:42px">LATEST NEWS</h2>

<div class="abs news-photo" role="img" aria-label="Handshake beside a laptop on a desk" style="left:76px;top:1958px;background:linear-gradient(135deg,#efece6,#a79f92 55%,#3d3a36)"></div>
<div class="abs date" style="left:622px;top:1988px">25</div>
<div class="abs news-title" style="left:724px;top:1998px">Lorem Ipsum is simply dummy text.</div>
<div class="abs meta" style="left:724px;top:2039px">
  <span><svg width="20" height="12" viewBox="0 0 20 12"><path d="M1 6s4-5 9-5 9 5 9 5-4 5-9 5-9-5-9-5z" fill="none" stroke="#777" stroke-width="1.5"/><circle cx="10" cy="6" r="2.5" fill="#777"/></svg>24 Views</span>
  <span><svg width="18" height="16" viewBox="0 0 18 16"><path d="M1 1h16v10H7l-4 4v-4H1z" fill="none" stroke="#777" stroke-width="1.5"/><path d="M4 5h10M4 8h7" stroke="#777"/></svg>16 Comments</span>
</div>
<p class="abs news-text" style="left:625px;top:2087px">Lorem Ipsum is simply dummy text of the printing and typesetting industry. Lorem Ipsum has been the industry's standard dummy text ever since the 1500s, when an unknown printer took a galley of type and scrambled it to make a type specimen book. It has survived not only five centuries, but also the leap into electronic typesetting.</p>

<div class="abs news-title" style="left:97px;top:2337px">Lorem Ipsum is simply dummy text.</div>
<div class="abs date" style="left:508px;top:2327px">25</div>
<div class="abs meta" style="left:222px;top:2378px">
  <span><svg width="20" height="12" viewBox="0 0 20 12"><path d="M1 6s4-5 9-5 9 5 9 5-4 5-9 5-9-5-9-5z" fill="none" stroke="#777" stroke-width="1.5"/><circle cx="10" cy="6" r="2.5" fill="#777"/></svg>24 Views</span>
  <span><svg width="18" height="16" viewBox="0 0 18 16"><path d="M1 1h16v10H7l-4 4v-4H1z" fill="none" stroke="#777" stroke-width="1.5"/><path d="M4 5h10M4 8h7" stroke="#777"/></svg>16 Comments</span>
</div>
<p class="abs news-text" style="left:96px;top:2426px;text-align:right">Lorem Ipsum is simply dummy text of the printing and typesetting industry. Lorem Ipsum has been the industry's standard dummy text ever since the 1500s, when an unknown printer took a galley of type and scrambled it to make a type specimen book. It has survived not only five centuries, but also the leap into electronic typesetting.</p>
<div class="abs news-photo" role="img" aria-label="Silhouettes of business people talking in a bright office" style="left:622px;top:2298px;background:linear-gradient(180deg,#e8e4df,#8c8a8c 55%,#2e3340)"></div>

<footer class="abs footer">
  <div class="abs brand"><div class="mark"></div><div class="name">HALDEN</div><div class="sub">LEGAL</div></div>
  <h4 class="abs" style="left:441px;top:48px">Contact Info</h4>
  <ul class="abs contact-list">
    <li><svg width="16" height="20" viewBox="0 0 18 22"><path d="M9 1a7 7 0 0 1 7 7c0 5-7 13-7 13S2 13 2 8a7 7 0 0 1 7-7z" fill="none" stroke="#fff" stroke-width="2.5"/><circle cx="9" cy="8" r="2.5" fill="#fff"/></svg><span>Lorem Ipsum is simply dummy<br>text of the printing and typeset.</span></li>
    <li><svg width="20" height="18" viewBox="0 0 24 24"><path d="M6 2l4 4-2 3c1 3 4 6 7 7l3-2 4 4-3 4C10 21 3 14 2 5z" fill="#fff"/></svg><span>123 456 7890</span></li>
    <li><svg width="20" height="18" viewBox="0 0 20 20"><rect x="1" y="6" width="18" height="13" fill="#fff"/><rect x="5" y="1" width="10" height="6" fill="none" stroke="#fff" stroke-width="2"/><rect x="4" y="10" width="3" height="2" fill="#1e3a6b"/><rect x="9" y="10" width="3" height="2" fill="#1e3a6b"/><rect x="4" y="14" width="3" height="2" fill="#1e3a6b"/><rect x="9" y="14" width="3" height="2" fill="#1e3a6b"/></svg><span>123 456 78690</span></li>
    <li><svg width="20" height="18" viewBox="0 0 20 16"><rect x="1" y="2" width="18" height="13" rx="2" fill="#fff"/><path d="M1 4l9 6 9-6" fill="none" stroke="#1e3a6b" stroke-width="1.5"/></svg><span>info@halden_legal.com</span></li>
  </ul>
  <h4 class="abs" style="left:803px;top:48px">Map</h4>
  <div class="abs map" role="img" aria-label="Map of the office location"></div>
</footer>
<div class="abs copyright">©HALDEN LEGAL- 2018. All Rights Reserved.</div>

</body>
</html>
```